New Web Design Project

Number of Pages Required

1 page

Requirements
Must have
• An Overview / Background of the Business & Services(not for profit rescue animal farm)
• The Target Market / Audience you are trying to reach (animal lovers)
• Design Specifics; any preferences or ideas for Style, Colour, Imagery, etc (no preferences)

```html
<!DOCTYPE html>
<html lang="en">
<head>
<meta charset="utf-8">
<title>Rescue Farm – Register For Service</title>
<link href="https://fonts.googleapis.com/css2?family=Courgette&family=Open+Sans:wght@400;700&family=Mulish:wght@400;500&display=swap" rel="stylesheet">
<style>
  :root {
    --plum: #675d69;
    --frame-line: #9a8f9b;
    --field: #e4e1e5;
    --field-text: #6e6a70;
    --coral: #ff5050;
    --white: #ffffff;
    --paper: #f2f2f2;
    --ink: #111111;
    --rule: #b9b4ba;
    --meta: #9a9a9a;
  }
  * { box-sizing: border-box; margin: 0; padding: 0; }
  html, body { width: 1200px; height: 1000px; overflow: hidden; }
  body { position: relative; background: var(--paper); font-family: "Open Sans", Arial, sans-serif; }

  .register { position: absolute; left: 0; top: 0; width: 1200px; height: 492px; background: var(--plum); }
  .register-frame { position: absolute; left: 22px; top: -2px; width: 1156px; height: 471px; border: 1px solid var(--frame-line); }

  .section-title { position: absolute; left: 0; width: 1200px; text-align: center; font-family: "Courgette", cursive; font-weight: 400; font-size: 50px; line-height: 1; }
  .register .section-title { top: 26px; color: var(--white); }
  .blog .section-title { top: 578px; color: var(--ink); }

  .title-divider { position: absolute; left: 516px; width: 173px; height: 20px; }
  .register .title-divider { top: 82px; }
  .blog .title-divider { top: 633px; }
  .title-divider .rule { position: absolute; left: 0; bottom: 2px; width: 100%; height: 1px; background: var(--rule); }
  .register .title-divider .rule { background: var(--white); opacity: .8; }
  .title-divider .emblem { position: absolute; left: 76px; top: 0; width: 20px; height: 18px; border-radius: 50% 50% 45% 45%; background: var(--ink); }

  .service-form { position: absolute; left: 463px; top: 176px; width: 278px; }
  .field { position: relative; height: 33px; margin-bottom: 15px; background: var(--field); color: var(--field-text); font-size: 11px; line-height: 33px; padding-left: 13px; }
  .field svg { position: absolute; right: 11px; top: 14px; }
  .register-button { display: block; width: 278px; height: 33px; margin-top: 1px; border: 0; background: var(--coral); color: var(--white); font-family: "Open Sans", Arial, sans-serif; font-weight: 700; font-size: 11px; text-transform: uppercase; }

  .blog { position: absolute; left: 0; top: 492px; width: 1200px; height: 508px; }
  .post-card { position: absolute; top: 726px; width: 278px; height: 300px; background: var(--white); padding: 16px 15px; }
  .post-card:nth-of-type(1) { left: 162px; }
  .post-card:nth-of-type(2) { left: 463px; }
  .post-card:nth-of-type(3) { left: 765px; }
  .post-image { width: 248px; height: 203px; }
  .post-title { margin-top: 17px; font-family: "Mulish", Arial, sans-serif; font-weight: 500; font-size: 18px; color: var(--ink); }
  .post-title.is-active { color: var(--coral); }
  .post-meta { margin-top: 8px; font-size: 10px; color: var(--meta); }
</style>
</head>
<body>
  <section class="register">
    <div class="register-frame"></div>
    <h2 class="section-title">Register For Service</h2>
    <div class="title-divider"><span class="rule"></span><span class="emblem" role="img" aria-label="Small cat silhouette ornament"></span></div>
    <form class="service-form">
      <div class="field">Your Name</div>
      <div class="field">Email Address</div>
      <div class="field">Number of Guest
        <svg width="7" height="5" viewBox="0 0 7 5"><path d="M1 1l2.5 2.5L6 1" fill="none" stroke="#333" stroke-width="1.2"/></svg>
      </div>
      <div class="field">Choose Event
        <svg width="7" height="5" viewBox="0 0 7 5"><path d="M1 1l2.5 2.5L6 1" fill="none" stroke="#333" stroke-width="1.2"/></svg>
      </div>
      <button type="button" class="register-button">Register Now</button>
    </form>
  </section>

  <section class="blog">
    <h2 class="section-title" style="top:86px">Latest From Blog</h2>
    <div class="title-divider" style="top:141px"><span class="rule"></span><span class="emblem" role="img" aria-label="Small cat silhouette ornament"></span></div>
  </section>

  <article class="post-card">
    <div class="post-image" role="img" aria-label="Photo of a kitten and a beagle puppy sitting on tree stumps in grass" style="background:linear-gradient(160deg,#9cc24a,#6f9a2e 60%,#8a6a45)"></div>
    <h3 class="post-title">This is a Sticky Post</h3>
  </article>
  <article class="post-card">
    <div class="post-image" role="img" aria-label="Photo of a woman hugging a brown cow" style="background:linear-gradient(160deg,#8aa36a,#7a5a3e 55%,#4a3426)"></div>
    <h3 class="post-title">Standard Post Example</h3>
  </article>
  <article class="post-card">
    <div class="post-image" role="img" aria-label="Photo of three deer standing on a grassy meadow" style="background:linear-gradient(170deg,#4f7a3a,#6d9a4a 55%,#9a6a40)"></div>
    <h3 class="post-title is-active">Example Gallery Post</h3>
    <p class="post-meta">Posted June 12, 2024 by Admin</p>
  </article>
</body>
</html>
```